Business Card Design For A Cajun Seafood Restaurant

We are opening a cajun seafood restaurant in a week. We mainly serve cajun seafood which is orginally from Louisiana. We want design on both sides of a business card. I have menu on the website. You can go to www.reednkettle.example to check out our menu.

Restaurant name: Reed N' Kettle
Phone: +1 (555) 304-7712
Address: 48206 Ludlow Row, #7, Bexmoor Flats, Ca90000
Email: reednkettle@mailbox.example
Website: www.reednkettle.example

Maybe add social media icons (facebook, instagram) if looks nice on the business card.
facebook.com/reednkettle
instagram.com/reednkettle or @reednkettle

Attached is the logo and other business card samples that I like.

```html
<!DOCTYPE html>
<html lang="en">
<head>
<meta charset="utf-8">
<title>Reed N' Kettle — Business Card</title>
<link rel="stylesheet" href="https://fonts.googleapis.com/css2?family=Open+Sans:wght@400;600;700&display=swap">
<style>
  :root {
    --page: #3a3633;
    --card: #121212;
    --ink: #e9e6e2;
    --accent: #e8772a;
    --gold: #f3b51b;
    --art-light: #f08a3c;
    --art-dark: #c9531c;
  }
  * { box-sizing: border-box; margin: 0; padding: 0; }
  html, body {
    width: 1200px; height: 900px; overflow: hidden;
    background: var(--page);
    font-family: "Open Sans", Arial, sans-serif;
  }
  .stage {
    width: 1200px; height: 900px;
    display: flex; flex-direction: column;
    align-items: center; justify-content: center; gap: 40px;
  }
  .card {
    width: 640px; height: 366px;
    background: var(--card);
    position: relative;
    box-shadow: 0 10px 28px rgba(0,0,0,.45);
  }
  /* back side */
  .card-back .mascot-art {
    position: absolute; left: 70px; top: 80px;
    width: 220px; height: 200px;
    border-radius: 45% 45% 40% 40%;
    background: radial-gradient(circle at 50% 45%, var(--art-light), var(--art-dark) 75%);
  }
  .divider {
    position: absolute; left: 322px; top: 92px;
    width: 2px; height: 150px;
    background: linear-gradient(var(--accent), rgba(232,119,42,0));
  }
  .contact {
    position: absolute; left: 348px; top: 70px;
    color: var(--ink); font-size: 14px; line-height: 20px;
  }
  .address { margin-bottom: 6px; }
  .contact-list { list-style: none; }
  .contact-list li { display: flex; align-items: center; gap: 10px; }
  .contact-list.social { margin-top: 12px; }
  .icon { width: 12px; height: 12px; flex: none; }
  .icon-square { width: 12px; height: 12px; border-radius: 2px; background: var(--accent); flex: none; }
  /* front side */
  .card-front { display: flex; flex-direction: column; align-items: center; justify-content: center; }
  .card-front .mascot-art {
    width: 150px; height: 120px;
    border-radius: 45% 45% 40% 40%;
    background: radial-gradient(circle at 50% 40%, var(--gold) 0 18%, var(--art-light) 35%, var(--art-dark) 80%);
    margin-bottom: 8px;
  }
  .brand-name {
    font-size: 38px; font-weight: 700; letter-spacing: 1px;
    color: var(--gold); text-transform: uppercase; line-height: 1.1;
  }
  .tagline {
    font-size: 15px; font-weight: 700; letter-spacing: 1px;
    color: var(--ink); text-transform: uppercase; margin-top: 4px;
  }
</style>
</head>
<body>
<main class="stage">
  <section class="card card-back">
    <div class="mascot-art" role="img" aria-label="Illustrated orange crab mascot holding an ear of corn"></div>
    <div class="divider"></div>
    <div class="contact">
      <p class="address">48206 Ludlow Row, #7,<br>Bexmoor Flats, Ca90000</p>
      <ul class="contact-list">
        <li>
          <svg class="icon" viewBox="0 0 12 12"><path d="M2 1l2 0 1 3-1.5 1a6 6 0 0 0 3.5 3.5L8 7l3 1v2c0 .6-.4 1-1 1A9 9 0 0 1 1 2c0-.6.4-1 1-1z" fill="var(--accent)"/></svg>
          +1 (555) 304-7712
        </li>
        <li>
          <svg class="icon" viewBox="0 0 12 12"><rect x="0.5" y="2" width="11" height="8" rx="1" fill="var(--accent)"/><path d="M1 3l5 4 5-4" stroke="var(--card)" stroke-width="1" fill="none"/></svg>
          reednkettle@mailbox.example
        </li>
        <li>
          <svg class="icon" viewBox="0 0 12 12"><circle cx="6" cy="6" r="5.5" fill="var(--accent)"/><path d="M.5 6h11M6 .5c-3 3-3 8 0 11M6 .5c3 3 3 8 0 11" stroke="var(--card)" stroke-width=".8" fill="none"/></svg>
          www.reednkettle.example
        </li>
      </ul>
      <ul class="contact-list social">
        <li><span class="icon-square"></span>reednkettle</li>
        <li><span class="icon-square"></span>reednkettle</li>
      </ul>
    </div>
  </section>

  <section class="card card-front">
    <div class="mascot-art" role="img" aria-label="Crab mascot holding an ear of corn"></div>
    <h1 class="brand-name">Reed N' Kettle</h1>
    <p class="tagline">Cajun Seafood House</p>
  </section>
</main>
</body>
</html>
```